New Business Card for Web Design/Internet Marketing Company

Looking for a great looking new business card. We are a 10 year old web design, internet marketing and website management company that works mostly with small businesses.

Our new card needs to better match the colors and style of our website, be bold, extremely usable and slightly edgy.

Target Market(s)

Small/Medium businesses that have websites

Industry/Entity Type

Internet

Requirements
Must have
• Front and back design, full color, rounded corners please

Must use the colors/style of our website (JPG provided)

INFO FOR CARDS (as readable as possible please)
Mark Lenner
President/CEO
mark@trelvanmedia.example
Phone: 520-381-7459
Toll Free: 866-381-7459
Address: 4315 W. Calloway Ave. Ste. 140, Tucson, AZ 85792

THINGS I WANT TO PROMOTE (if there is room):
1. Our Website - www.trelvanmedia.example

2. Social Media
Twitter: @trelvanmedia
Facebook: www.facebook.com/trelvanmedia

3. Our Services
Web Design
Internet Marketing
Website Management

```html
<!DOCTYPE html>
<html lang="en">
<head>
<meta charset="utf-8">
<title>Trelvan Media – Business Card</title>
<link rel="stylesheet" href="https://fonts.googleapis.com/css2?family=Open+Sans:wght@400;600;700&display=swap">
<style>
  :root {
    --orange: #f5843a;
    --blue: #1b8fcb;
    --white: #ffffff;
    --stage: #ecebe8;
    --ink-soft: #5a5a5a;
  }
  * { margin: 0; padding: 0; box-sizing: border-box; }
  html, body { width: 1200px; height: 1021px; overflow: hidden; }
  body {
    background: var(--stage);
    font-family: "Open Sans", Arial, sans-serif;
    position: relative;
  }
  .card {
    position: absolute;
    width: 752px;
    height: 428px;
    overflow: hidden;
    box-shadow: 0 2px 6px rgba(0,0,0,0.25);
  }

  /* Front */
  .card-front { left: 70px; top: 57px; background: var(--white); }
  .front-brand {
    position: absolute; left: 0; right: 0; top: 70px;
    text-align: center;
  }
  .brand-name {
    font-weight: 700; font-size: 58px; color: var(--blue);
    letter-spacing: -1px; line-height: 1;
  }
  .brand-tagline {
    margin-top: 8px; padding-left: 300px;
    font-size: 18px; color: var(--ink-soft); font-weight: 400;
  }
  .holder {
    position: absolute; left: 0; right: 0; top: 216px;
    text-align: center; line-height: 1;
  }
  .holder-name { font-weight: 700; font-size: 27px; color: var(--orange); }
  .holder-title { font-weight: 400; font-size: 21px; color: var(--blue); margin-left: 4px; }
  .rule { position: absolute; left: 0; right: 0; top: 263px; height: 3px; background: var(--blue); }
  .front-band {
    position: absolute; left: 0; right: 0; top: 272px; bottom: 0;
    background: var(--orange); color: var(--white);
  }
  .address {
    position: absolute; right: 397px; top: 42px;
    text-align: right; font-size: 18px; line-height: 27px;
  }
  .divider {
    position: absolute; left: 378px; top: 18px; width: 1px; height: 128px;
    background: rgba(255,255,255,0.6);
  }
  .contacts {
    position: absolute; left: 399px; top: 26px;
    list-style: none; font-size: 18px; line-height: 27px;
  }
  .contacts li { display: flex; align-items: center; gap: 10px; }
  .contacts svg { width: 14px; height: 14px; flex: none; }

  /* Back */
  .card-back { left: 363px; top: 523px; background: var(--orange); color: var(--white); }
  .back-brand {
    position: absolute; left: 0; right: 0; top: 100px;
    text-align: center; font-weight: 700; font-size: 96px;
    letter-spacing: -2px; line-height: 1;
  }
  .services {
    position: absolute; left: 0; right: 0; top: 278px;
    text-align: center; font-weight: 700; font-size: 24px; line-height: 32px;
  }
  .services span::before {
    content: ""; display: inline-block; width: 10px; height: 10px;
    border-radius: 50%; background: var(--white);
    margin: 0 8px 4px 14px; vertical-align: middle;
  }
  .social {
    position: absolute; left: 0; right: 0; top: 356px;
    display: flex; justify-content: center; gap: 28px;
    font-size: 24px; font-weight: 400;
  }
  .social-item { display: flex; align-items: center; gap: 8px; }
  .social-item i {
    display: inline-block; width: 20px; height: 20px; border-radius: 2px;
    background: var(--white); opacity: 0.85;
  }
</style>
</head>
<body>
  <section class="card card-front">
    <div class="front-brand">
      <div class="brand-name">Trelvan Media</div>
      <div class="brand-tagline">Grow your Website</div>
    </div>
    <div class="holder">
      <span class="holder-name">Mark Lenner ,</span><span class="holder-title">President/CEO</span>
    </div>
    <div class="rule"></div>
    <div class="front-band">
      <p class="address">4315 W. Calloway Ave. Ste. 140<br>Tucson, AZ 85792</p>
      <div class="divider"></div>
      <ul class="contacts">
        <li><svg viewBox="0 0 14 14"><path d="M3 1l2 3-1.3 1.3a8 8 0 0 0 5 5L10 9l3 2-1 2C6 13 1 8 1 2z" fill="#fff"/></svg>866-381-7459</li>
        <li><svg viewBox="0 0 14 14"><path d="M3 1l2 3-1.3 1.3a8 8 0 0 0 5 5L10 9l3 2-1 2C6 13 1 8 1 2z" fill="#fff"/></svg>520-381-7459</li>
        <li><svg viewBox="0 0 14 14"><rect x="1" y="3" width="12" height="8" fill="#fff"/><path d="M1 3l6 5 6-5" stroke="#f5843a" stroke-width="1.2" fill="none"/></svg>mark@trelvanmedia.example</li>
        <li><svg viewBox="0 0 14 14"><circle cx="7" cy="7" r="6" fill="#fff"/><path d="M1 7h12M7 1c-3 3-3 9 0 12M7 1c3 3 3 9 0 12" stroke="#f5843a" stroke-width="1" fill="none"/></svg>www.trelvanmedia.example</li>
      </ul>
    </div>
  </section>

  <section class="card card-back">
    <div class="back-brand">Trelvan</div>
    <div class="services">
      <span>Web Design</span><span>Internet Marketing</span><br>
      <span>Website Management</span>
    </div>
    <div class="social">
      <div class="social-item"><i></i>@trelvanmedia</div>
      <div class="social-item"><i></i>trelvanmedia</div>
    </div>
  </section>
</body>
</html>
```